Silver Heron Motor Works needs a logo design

I'm after a logo design for a new Female owned automotive repair workshop in the Queanbeyan/Canberra Australia Area.
We offer repairs on all passenger cars, 4wds and light trucks emphasising a strong honest work ethic and a genuine interest in the customer and their vehicles needs. With business details on the front of the card and what we offer on the back.
I would like a design with a phoenix in multiple colours maybe hovering over a flaming wheel or a car with wheels flaming with the phoenix hovering up out of the flames
All Vehicle users
Automotive
On the front
Silver Heron Motor
Marla Pettigrew Owner/ Mechanic 0481736055
email marla@silverheronmotor.com.au
Website www.silverheronmotorworks.com.au
On the back
All Cars, 4WDs, Light trucks, makes and models
Log book servicing
General vehicle servicing
Major vehicle servicing
brake and clutch servicing and repairs
Suspension repairs
cooling systems
All major and minor mechanical repairs
minor electrical rewiring and repairs
Designer to choose colors to be used in the design.

```html
<!DOCTYPE html>
<html lang="en">
<head>
<meta charset="utf-8">
<title>Silver Heron Motor – Business Card</title>
<link href="https://fonts.googleapis.com/css2?family=Montserrat:wght@400;500&family=Saira+Condensed:wght@600&display=swap" rel="stylesheet">
<style>
  :root{
    --backdrop:#dcdcda;
    --card-dark:#1c1c1d;
    --card-mid:#38393b;
    --orange:#f08a1c;
    --orange-deep:#e4591a;
    --flame-yellow:#f7b531;
    --teal:#2fa88a;
    --white:#f2f2f2;
    --grey-text:#d8d8d8;
  }
  *{box-sizing:border-box;margin:0;padding:0}
  html,body{width:1200px;height:1200px;overflow:hidden;background:var(--backdrop)}
  .canvas{position:relative;width:1200px;height:1200px}
  .card{
    position:absolute;left:150px;width:900px;height:515px;border-radius:30px;overflow:hidden;
    background:radial-gradient(ellipse at 60% 40%,var(--card-mid) 0%,#262628 55%,var(--card-dark) 100%);
    box-shadow:0 10px 24px rgba(0,0,0,.25);
  }
  .card::before{
    content:"";position:absolute;inset:0;
    background-image:radial-gradient(rgba(0,0,0,.35) 1.2px,transparent 1.6px);
    background-size:8px 8px;opacity:.6;
  }
  .card--front{top:50px}
  .card--back{top:630px}

  .art{position:absolute;z-index:0}
  .art--phoenix{left:40px;top:40px;width:300px;height:380px;border-radius:46% 46% 30% 30%;
    background:linear-gradient(160deg,var(--teal) 0%,#4fae6a 35%,var(--flame-yellow) 65%,var(--orange-deep) 100%);opacity:.9}
  .art--flame-wheel{left:-30px;top:-20px;width:200px;height:300px;border-radius:0 0 60% 40%;
    background:linear-gradient(200deg,var(--flame-yellow) 0%,var(--orange) 45%,var(--orange-deep) 80%,#2a1a10 100%);opacity:.9}

  .brand{position:absolute;z-index:1;right:60px;top:95px;display:flex;align-items:center;gap:14px;
    font-family:"Montserrat",sans-serif;font-weight:500;font-size:44px;color:var(--orange);letter-spacing:1px}
  .brand__dot{width:18px;height:18px;border-radius:50%;background:var(--orange)}

  .contact{position:absolute;z-index:1;right:60px;top:250px;text-align:right;font-family:"Montserrat",sans-serif}
  .contact__name{font-size:34px;font-weight:500;color:var(--orange);letter-spacing:3px;text-transform:uppercase}
  .contact__role{font-size:26px;color:var(--white);letter-spacing:2px;text-transform:uppercase;margin-top:4px}
  .contact__line{display:flex;justify-content:flex-end;align-items:center;gap:12px;font-size:24px;color:var(--grey-text);margin-top:14px;letter-spacing:1px}
  .contact__icon{width:26px;height:26px;flex:none}

  .services{position:absolute;z-index:1;right:60px;top:60px;text-align:right;list-style:none;
    font-family:"Saira Condensed",sans-serif;font-weight:600;font-size:33px;line-height:1.17;color:var(--orange);text-transform:uppercase}
  .website{position:absolute;z-index:1;right:60px;bottom:40px;font-family:"Saira Condensed",sans-serif;font-weight:600;
    font-size:34px;color:var(--white);text-transform:uppercase;letter-spacing:.5px}
</style>
</head>
<body>
<main class="canvas">

  <section class="card card--front" aria-label="Business card front">
    <div class="art art--phoenix" role="img" aria-label="Multicoloured phoenix rising out of flames"></div>
    <div class="brand"><span class="brand__dot"></span>Silver Heron Motor</div>
    <div class="contact">
      <p class="contact__name">Marla Pettigrew</p>
      <p class="contact__role">Owner/ Mechanic</p>
      <p class="contact__line">0481736055
        <svg class="contact__icon" viewBox="0 0 24 24" aria-hidden="true"><circle cx="12" cy="12" r="12" fill="var(--orange)"/><path d="M8 6l2.2 0 1 3-1.4 1.2a8 8 0 0 0 4 4l1.2-1.4 3 1v2.2c0 .6-.5 1-1 1A11 11 0 0 1 7 7c0-.6.4-1 1-1z" fill="#1c1c1d"/></svg>
      </p>
      <p class="contact__line">marla@silverheronmotor.com.au
        <svg class="contact__icon" viewBox="0 0 24 24" aria-hidden="true"><circle cx="12" cy="12" r="12" fill="var(--orange)"/><rect x="6" y="8" width="12" height="8" rx="1" fill="#1c1c1d"/><path d="M6.5 8.5L12 13l5.5-4.5" stroke="var(--orange)" stroke-width="1.4" fill="none"/></svg>
      </p>
    </div>
  </section>

  <section class="card card--back" aria-label="Business card back">
    <div class="art art--flame-wheel" role="img" aria-label="Flaming wheel with rising flames"></div>
    <ul class="services">
      <li>All cars, 4WDs, light trucks, makes and models</li>
      <li>Log book servicing</li>
      <li>General vehicle servicing</li>
      <li>Major vehicle servicing</li>
      <li>Brake and clutch servicing and repairs</li>
      <li>Suspension repairs</li>
      <li>Cooling systems</li>
      <li>All major and minor mechanical repairs</li>
      <li>Minor electrical rewiring and repairs</li>
    </ul>
    <p class="website">www.silverheronmotorworks.com.au</p>
  </section>

</main>
</body>
</html>
```